Kelbrook Plumbing flyer

I want to incorporate our logo design into a new flyer promoting the business and advertising products that we install.
We install hot water systems, Air-conditioning systems and central heating systems. Along with other aspects of plumbing such as gasfitting, roofing, sanitary and drainage
I would like the background to be the same as our business cards with the water effect and colours.

Requirements
Must have
• Logo
24/7 Emergency call out
Aspects of plumbing we do
- Hot water systems
- Central Heating
- Solar hot water systems/ heat pump systems
- Gasfitting
- Drainage
- Roofing
- Air-Conditioning
Nice to have
• Pictures of hot water systems and air-conditioning system
$30 off voucher when producing this flyer (limit 1 per house hold)

```html
<!DOCTYPE html>
<html lang="en">
<head>
<meta charset="UTF-8">
<title>Kelbrook Plumbing Flyer</title>
<link href="https://fonts.googleapis.com/css2?family=Montserrat:wght@500;600;800;900&display=swap" rel="stylesheet">
<style>
  :root {
    --navy: #03284f;
    --navy-deep: #022244;
    --sky: #0aa0e2;
    --mid-blue: #0b7ccc;
    --charcoal: #48494b;
    --charcoal-mid: #3a3b3d;
    --charcoal-dark: #27282a;
    --white: #ffffff;
  }
  html, body { margin: 0; padding: 0; overflow: hidden; background: var(--white); }
  .flyer {
    position: relative;
    width: 849px;
    height: 1200px;
    overflow: hidden;
    background: var(--navy);
    font-family: "Montserrat", sans-serif;
    color: var(--white);
  }
  .water-backdrop {
    position: absolute; left: 0; top: 0; width: 849px; height: 440px;
    background:
      radial-gradient(ellipse at 75% 30%, var(--charcoal) 0%, transparent 55%),
      radial-gradient(ellipse at 20% 70%, var(--charcoal-mid) 0%, transparent 60%),
      linear-gradient(160deg, var(--charcoal-mid) 0%, var(--charcoal-dark) 100%);
  }
  .photo { position: absolute; left: 437px; width: 412px; }
  .photo-aircon {
    top: 410px; height: 370px;
    background: linear-gradient(135deg, #c9b9a2 0%, #e8e2d8 45%, #b7b2aa 100%);
  }
  .photo-sink {
    top: 760px; height: 300px;
    background: linear-gradient(160deg, #eef0f2 0%, #d9dcdf 55%, #9ea3a8 100%);
  }
  .waves { position: absolute; left: 0; top: 0; width: 849px; height: 1200px; }
  .brand-mark {
    position: absolute; left: 42px; top: 48px;
    width: 146px; height: 146px; border-radius: 50%; background: var(--sky);
  }
  .brand-text { position: absolute; left: 209px; top: 76px; }
  .brand-name {
    margin: 0; font-weight: 900; color: var(--sky);
    text-transform: uppercase; letter-spacing: 0.5px;
  }
  .brand-name-first { display: block; font-size: 66px; line-height: 66px; }
  .brand-name-second { display: block; font-size: 56px; line-height: 56px; }
  .brand-tagline {
    margin: 8px 0 0; font-weight: 800; font-size: 24px; color: var(--white);
    text-transform: uppercase; letter-spacing: 0.5px;
  }
  .headline { position: absolute; left: 32px; top: 400px; margin: 0; }
  .headline-lead, .headline-tail {
    display: block; color: var(--sky); font-weight: 900; font-size: 37px; line-height: 44px;
  }
  .headline-main {
    display: block; font-weight: 900; font-size: 56px; line-height: 52px; letter-spacing: 0.5px;
  }
  .services-label {
    position: absolute; left: 32px; top: 544px; margin: 0;
    color: var(--sky); font-weight: 900; font-size: 25px;
  }
  .services {
    position: absolute; left: 32px; top: 640px; margin: 0; padding: 0; list-style: none;
  }
  .services li {
    display: flex; align-items: center; gap: 14px;
    height: 42.4px; font-weight: 500; font-size: 22.5px; letter-spacing: 0.6px;
  }
  .tick { width: 23px; height: 23px; flex: none; }
  .call-banner {
    position: absolute; left: 0; top: 1061px; width: 620px; height: 76px;
    background: var(--sky);
    clip-path: polygon(0 0, 100% 0, 95.3% 100%, 0 100%);
    display: flex; align-items: center;
  }
  .call-number {
    margin: 0 0 0 24px; font-weight: 900; font-size: 42px; letter-spacing: 0.3px;
  }
  .licence { position: absolute; left: 651px; top: 1106px; }
  .licence-label { display: block; font-weight: 500; font-size: 14.5px; letter-spacing: 0.3px; }
  .licence-number { display: block; font-weight: 600; font-size: 38px; line-height: 1.1; letter-spacing: 0.5px; }
  .contact {
    position: absolute; left: 25px; top: 1157px; margin: 0;
    font-weight: 500; font-size: 16.5px; letter-spacing: 0.4px;
  }
</style>
</head>
<body>
<main class="flyer">
  <div class="water-backdrop" role="img" aria-label="Dark charcoal background covered in water droplets"></div>

  <div class="photo photo-aircon" role="img" aria-label="Photo of a technician checking an air-conditioning unit with pressure gauges"></div>
  <div class="photo photo-sink" role="img" aria-label="Photo of a plumber tightening pipes under a sink with a red wrench"></div>

  <svg class="waves" viewBox="0 0 849 1200" aria-hidden="true">
    <path fill="var(--mid-blue)" d="M0 290 C150 230 300 225 450 285 C600 345 720 420 849 370 L849 500 C760 540 650 520 560 470 C420 390 250 300 0 320 Z"/>
    <path fill="var(--sky)" d="M0 300 C160 260 320 265 460 330 C600 400 720 450 849 400 L849 470 C740 520 640 500 540 450 C400 370 220 300 0 320 Z"/>
    <path fill="var(--navy)" d="M0 322 C200 285 380 305 520 385 C640 450 760 480 849 440 L849 500 L437 520 L437 1060 L0 1060 Z"/>
    <path fill="var(--navy)" d="M437 400 L560 410 C640 440 720 470 849 445 L849 480 C800 510 740 520 660 505 C580 490 510 440 437 415 Z"/>
    <path fill="var(--sky)" d="M560 515 C680 540 780 510 849 470 L849 500 C780 540 680 560 560 515 Z"/>
    <path fill="var(--navy)" d="M440 718 C520 760 600 785 690 786 C770 787 820 765 849 748 L849 800 C800 825 740 838 680 836 C580 832 500 790 440 780 Z"/>
    <rect fill="var(--navy-deep)" x="0" y="1060" width="849" height="140"/>
  </svg>

  <span class="brand-mark"></span>
  <header class="brand-text">
    <h1 class="brand-name"><span class="brand-name-first">Kelbrook</span><span class="brand-name-second">Plumbing</span></h1>
    <p class="brand-tagline">&amp; Air-Conditioning</p>
  </header>

  <h2 class="headline">
    <span class="headline-lead">Need a Premium</span>
    <span class="headline-main">PLUMBING</span>
    <span class="headline-tail">Service?</span>
  </h2>

  <p class="services-label">We Provide:</p>

  <ul class="services">
    <li><svg class="tick" viewBox="0 0 24 24"><circle cx="12" cy="12" r="12" fill="#fff"/><path d="M7 12.5l3.3 3.3L17 8.5" fill="none" stroke="#03284f" stroke-width="2.2" stroke-linecap="round" stroke-linejoin="round"/></svg>PLUMBING &amp; GASFITTING</li>
    <li><svg class="tick" viewBox="0 0 24 24"><circle cx="12" cy="12" r="12" fill="#fff"/><path d="M7 12.5l3.3 3.3L17 8.5" fill="none" stroke="#03284f" stroke-width="2.2" stroke-linecap="round" stroke-linejoin="round"/></svg>AIR-CONDITIONING</li>
    <li><svg class="tick" viewBox="0 0 24 24"><circle cx="12" cy="12" r="12" fill="#fff"/><path d="M7 12.5l3.3 3.3L17 8.5" fill="none" stroke="#03284f" stroke-width="2.2" stroke-linecap="round" stroke-linejoin="round"/></svg>BLOCKED DRAINS</li>
    <li><svg class="tick" viewBox="0 0 24 24"><circle cx="12" cy="12" r="12" fill="#fff"/><path d="M7 12.5l3.3 3.3L17 8.5" fill="none" stroke="#03284f" stroke-width="2.2" stroke-linecap="round" stroke-linejoin="round"/></svg>HOT WATER SYSTEMS</li>
    <li><svg class="tick" viewBox="0 0 24 24"><circle cx="12" cy="12" r="12" fill="#fff"/><path d="M7 12.5l3.3 3.3L17 8.5" fill="none" stroke="#03284f" stroke-width="2.2" stroke-linecap="round" stroke-linejoin="round"/></svg>CENTRAL HEATING</li>
    <li><svg class="tick" viewBox="0 0 24 24"><circle cx="12" cy="12" r="12" fill="#fff"/><path d="M7 12.5l3.3 3.3L17 8.5" fill="none" stroke="#03284f" stroke-width="2.2" stroke-linecap="round" stroke-linejoin="round"/></svg>ROOFING</li>
    <li><svg class="tick" viewBox="0 0 24 24"><circle cx="12" cy="12" r="12" fill="#fff"/><path d="M7 12.5l3.3 3.3L17 8.5" fill="none" stroke="#03284f" stroke-width="2.2" stroke-linecap="round" stroke-linejoin="round"/></svg>SANITARY AND DRAINAGE</li>
    <li><svg class="tick" viewBox="0 0 24 24"><circle cx="12" cy="12" r="12" fill="#fff"/><path d="M7 12.5l3.3 3.3L17 8.5" fill="none" stroke="#03284f" stroke-width="2.2" stroke-linecap="round" stroke-linejoin="round"/></svg>SOLAR HOT WATER</li>
  </ul>

  <div class="call-banner">
    <p class="call-number">CALL US : 0400 517 239</p>
  </div>

  <div class="licence">
    <span class="licence-label">Licence Number</span>
    <span class="licence-number">208461</span>
  </div>

  <p class="contact">www.kelbrookplumbing.com | hello@kelbrookplumbing.com</p>
</main>
</body>
</html>
```